New Home Subdivision Sign for Larchmere Fields

I need a sign designed for a new home subdivision called Larchmere Fields. It is a family subdivision with many kids. Homes are average size. It is located in a small town.
I will have a tag line so please leave a space for just one sentence.
I have attached the subdivision logo (Larchmere Fields) and the builder logo (Belvix Homes). The subdivision logo has two options (vertical and horizontal), choose whichever fits best for you.
I will need a spot on the sign for a site map. The site map is not completed yet but should be ready in a week and I can send it to you then.
There are no roses in this subdivision. The name is because the original owner of the land had the last name Halbrook. The logo plays off the name but please no other "rose" inspiration
Along the very bottom (no more than 1 foot tall) I need my real estate company info. When you get to that point I will send the files and info but it should all fit within the bottom banner.
Sign is 5' x 8'
Thank you
Target Market(s)
Families
Industry/Entity Type
New Home Construction
Requirements
Must have
- Larchmere Fields logo, space for Realtor info in bottom 12 inches, space for site map that will be provided next week.
Nice to have
- I like the idea of a picture of a family. I also need a tag line for the subdivision so I'm open to ideas on that too

```html
<!DOCTYPE html>
<html lang="en">
<head>
<meta charset="utf-8">
<title>Larchmere Fields – Subdivision Sign</title>
<link rel="stylesheet" href="https://fonts.googleapis.com/css2?family=Montserrat:wght@400;500;600;700&family=Playball&display=swap">
<style>
  :root {
    --maroon: #7d0a22;
    --green: #6db36a;
    --ink: #1b1b1b;
    --photo-light: #fbf2e2;
    --photo-mid: #f1d9ae;
    --photo-deep: #d9b77c;
    --paper: #f6f6f6;
    --map-tint: #cfe9e6;
  }
  * { box-sizing: border-box; margin: 0; padding: 0; }
  html, body { width: 818px; height: 1200px; overflow: hidden; background: #ffffff; }
  .sign {
    position: relative;
    width: 818px;
    height: 1200px;
    overflow: hidden;
    background: linear-gradient(180deg, #ffffff 0%, var(--paper) 70%, #ededed 100%);
    font-family: "Montserrat", sans-serif;
    color: var(--ink);
  }
  .hero-art { position: absolute; inset: 0; width: 818px; height: 1200px; }

  .subdivision-name {
    position: absolute;
    top: 88px;
    left: 0;
    width: 818px;
    display: flex;
    align-items: center;
    justify-content: center;
    gap: 24px;
  }
  .subdivision-name .mark {
    width: 90px; height: 90px;
    border-radius: 50%;
    background: var(--maroon);
  }
  .subdivision-name .words {
    color: var(--maroon);
    font-weight: 600;
    line-height: 1;
    text-align: center;
  }
  .subdivision-name .line-1 { font-size: 56px; letter-spacing: 0.03em; display: block; }
  .subdivision-name .line-2 { font-size: 34px; letter-spacing: 0.32em; display: block; margin-top: 12px; margin-right: -0.32em; }

  .tagline {
    position: absolute;
    top: 236px;
    left: 0;
    width: 818px;
    text-align: center;
    font-family: "Playball", cursive;
    font-size: 64px;
    line-height: 1;
  }
  .tagline .lead { color: var(--maroon); }
  .tagline .tail { color: var(--green); }

  .builder-name {
    position: absolute;
    top: 812px;
    left: 0;
    width: 818px;
    text-align: center;
  }
  .builder-name .main {
    display: block;
    font-size: 112px;
    font-weight: 500;
    letter-spacing: 0.04em;
    line-height: 1;
    color: var(--ink);
  }
  .builder-name .sub {
    display: inline-flex;
    align-items: center;
    gap: 22px;
    margin-top: 14px;
    font-size: 30px;
    font-weight: 500;
    letter-spacing: 1.05em;
    color: var(--ink);
  }
  .builder-name .sub::before,
  .builder-name .sub::after {
    content: "";
    width: 58px;
    height: 3px;
    background: var(--ink);
  }
  .builder-name .sub span { margin-right: -1.05em; }

  .agent-info { position: absolute; left: 59px; top: 1000px; width: 300px; }
  .agent-info .company-slot { font-size: 14.5px; font-weight: 500; letter-spacing: 0.02em; }
  .agent-info .agent-name {
    margin-top: 14px;
    width: 180px;
    height: 26px;
    padding-left: 15px;
    background: var(--green);
    clip-path: polygon(0 0, 88% 0, 100% 100%, 0 100%);
    color: #ffffff;
    font-size: 17px;
    font-weight: 700;
    line-height: 26px;
    letter-spacing: 0.03em;
  }
  .agent-info .agent-phone {
    width: 272px;
    height: 38px;
    background: var(--maroon);
    color: #ffffff;
    display: flex;
    align-items: center;
    gap: 8px;
    padding-left: 14px;
    font-size: 26px;
    font-weight: 700;
  }
  .agent-info .contact-list { list-style: none; margin-top: 14px; }
  .agent-info .contact-list li {
    display: flex; align-items: center; gap: 10px;
    font-size: 15.5px; font-weight: 500; height: 23px;
  }
  .agent-info .contact-list svg { width: 15px; height: 15px; }
  .agent-info .member-badge {
    position: absolute; left: 241px; top: 116px;
    width: 30px; height: 34px; background: var(--ink);
  }

  .divider {
    position: absolute; left: 388px; top: 990px;
    width: 2px; height: 174px; background: var(--maroon);
  }
  .site-map-slot {
    position: absolute; left: 420px; top: 994px;
    width: 334px; height: 154px;
    background: linear-gradient(135deg, #e4f3f1 0%, var(--map-tint) 50%, #e8f4f2 100%);
    display: flex; align-items: center; justify-content: center;
  }
  .site-map-slot .label { font-size: 36px; font-weight: 500; color: #000000; }
</style>
</head>
<body>
<main class="sign">
  <svg class="hero-art" viewBox="0 0 818 1200">
    <defs>
      <linearGradient id="heroTone" x1="0" y1="0" x2="0" y2="1">
        <stop offset="0" stop-color="#fdf8ef"/>
        <stop offset="0.5" stop-color="#f4e2c2"/>
        <stop offset="1" stop-color="#e3c48f"/>
      </linearGradient>
    </defs>
    <path class="band-maroon" fill="#7d0a22" d="M0 0 H818 V705 C700 760 520 800 400 795 C250 790 90 730 0 688 Z"/>
    <path class="band-green" fill="#6db36a" d="M0 0 H818 V625 C660 720 480 775 340 772 C200 768 80 720 0 680 Z"/>
    <path class="band-white" fill="#ffffff" d="M0 0 H818 V560 C650 668 460 742 300 735 C170 730 60 705 0 676 Z"/>
    <path class="hero-photo" fill="url(#heroTone)" role="img" aria-label="Photo of a happy family of five running together across an open field at sunset"
          d="M0 0 H818 V553 C650 660 450 740 300 727 C180 718 60 700 0 674 Z"/>
  </svg>

  <div class="subdivision-name">
    <div class="mark"></div>
    <div class="words">
      <span class="line-1">LARCHMERE</span>
      <span class="line-2">FIELDS</span>
    </div>
  </div>

  <p class="tagline"><span class="lead">Home away</span> <span class="tail">From Home</span></p>

  <div class="builder-name">
    <span class="main">BELVIX</span>
    <span class="sub"><span>HOMES</span></span>
  </div>

  <section class="agent-info">
    <p class="company-slot">REAL ESTATE COMPANY LOGO</p>
    <p class="agent-name">MARA QUILL</p>
    <p class="agent-phone">
      <svg width="24" height="24" viewBox="0 0 24 24" aria-hidden="true">
        <circle cx="12" cy="12" r="10.5" fill="none" stroke="#fff" stroke-width="2"/>
        <path d="M8.5 6.5 l2 2.5 -1.2 1.3 c0.8 1.7 2 2.9 3.6 3.7 l1.3-1.2 2.5 2 -1.3 1.8 c-4-0.6-7.6-4.2-8.2-8.2z" fill="#fff"/>
      </svg>
      0198 765 432
    </p>
    <ul class="contact-list">
      <li>
        <svg viewBox="0 0 16 16" aria-hidden="true"><rect x="1" y="3" width="14" height="10" fill="none" stroke="#7d0a22" stroke-width="1.3"/><path d="M1 3 L8 9 L15 3" fill="none" stroke="#7d0a22" stroke-width="1.3"/></svg>
        info@fieldkeyrealty.com
      </li>
      <li>
        <svg viewBox="0 0 16 16" aria-hidden="true"><circle cx="8" cy="8" r="6.5" fill="none" stroke="#7d0a22" stroke-width="1.3"/><ellipse cx="8" cy="8" rx="3" ry="6.5" fill="none" stroke="#7d0a22" stroke-width="1.1"/><path d="M1.5 8 H14.5" stroke="#7d0a22" stroke-width="1.1"/></svg>
        www.fieldkeyrealty.com
      </li>
    </ul>
    <div class="member-badge"></div>
  </section>

  <div class="divider"></div>

  <div class="site-map-slot" role="img" aria-label="Subdivision site map with numbered lots">
    <span class="label">site map here</span>
  </div>
</main>
</body>
</html>
```